A website for Kovadrel Limited

We need a new and modern website for our company. We are engineering consultants and contractors (EPC) in the oil and gas industry and building services industry.
What we do:
Engineering, procurement, construction
Automation (safety and process)
Non-destructive testing
Training
We have an existing website and the content can be referred from there since we are remaking the website
For more information visit Kovadrel Limited Kenya

```html
<!DOCTYPE html>
<html lang="en">
<head>
<meta charset="utf-8">
<title>Kovadrel Limited</title>
<link href="https://fonts.googleapis.com/css2?family=Roboto:wght@400;500;700;900&display=swap" rel="stylesheet">
<style>
:root{
  --orange:#e4612b;
  --orange-deep:#c8431b;
  --orange-light:#f08a4f;
  --peach:#f6c9b4;
  --ink:#1f1f1f;
  --text:#555;
  --white:#fff;
  --footer:#2b2b2b;
  --line:#e3e3e3;
}
*{box-sizing:border-box;margin:0;padding:0}
html,body{width:1200px;height:3576px;overflow:hidden}
body{font-family:'Roboto',sans-serif;color:var(--ink);background:var(--white);position:relative}
.abs{position:absolute}
.btn{display:inline-block;background:var(--orange-deep);color:var(--white);font-size:15px;font-weight:500;padding:13px 22px;border-radius:4px}
.btn.light{background:var(--white);color:var(--orange-deep)}
.section-title{font-size:46px;font-weight:700;letter-spacing:1px;color:var(--ink)}
.body-text{font-size:15px;line-height:1.6;color:var(--text)}

/* header */
.site-header{left:0;top:0;width:1200px;height:140px;background:var(--white);z-index:5}
.brand{left:110px;top:18px;display:flex;align-items:center;gap:12px}
.brand-dot{width:46px;height:46px;border-radius:50%;background:var(--orange)}
.brand-name{font-size:26px;font-weight:700;color:var(--orange-deep);line-height:1}
.phone-pill{right:110px;top:0;background:var(--orange);color:var(--white);font-size:14px;font-weight:700;padding:9px 22px;border-radius:0 0 8px 8px;display:flex;gap:8px;align-items:center}
.main-nav{right:110px;top:64px;display:flex;gap:50px;font-size:17px}
.main-nav a{color:var(--ink);text-decoration:none}

/* hero */
.hero{left:0;top:110px;width:1200px;height:720px;background:linear-gradient(120deg,var(--orange-light) 0%,var(--orange) 45%,var(--orange-deep) 100%);clip-path:polygon(0 0,100% 0,100% 100%,0 84%)}
.hero-media{left:600px;top:150px;width:560px;height:600px;border-radius:30px;background:radial-gradient(circle at 55% 45%,#f3d9c4 0%,#b9775a 45%,rgba(200,67,27,0) 72%)}
.hero-copy{left:110px;top:220px;width:480px;color:var(--white)}
.hero-copy h1{font-size:66px;font-weight:900;line-height:1.08;text-transform:uppercase}
.hero-copy p{font-size:17px;font-weight:500;line-height:1.5;margin:34px 0 40px}

/* about */
.about-photo{left:112px;top:860px;width:490px;height:450px;border-radius:22px;background:linear-gradient(160deg,#cfd9e4 0%,#8ba2b8 45%,#3e5d86 100%)}
.about-copy{left:665px;top:900px;width:430px}
.about-copy p{margin-top:26px}
.peach-circle{border-radius:50%;background:var(--peach)}

/* what we do */
.services-band{left:0;top:1370px;width:1200px;height:800px;background:linear-gradient(180deg,var(--orange-light),var(--orange) 50%,var(--orange-deep));clip-path:polygon(0 10%,100% 0,100% 90%,0 100%)}
.services-intro{left:110px;top:1620px;width:370px;color:var(--white)}
.services-intro .section-title{color:var(--white)}
.services-intro p{color:var(--white);margin:26px 0 30px}
.service-card{width:270px;height:255px;background:var(--white);border-radius:8px;box-shadow:0 10px 24px rgba(0,0,0,.18);text-align:center;padding:40px 26px 0}
.service-card.active{background:var(--orange-deep);color:var(--white)}
.service-card h3{font-size:18px;font-weight:500;margin:22px 0 10px}
.service-card p{font-size:13px;line-height:1.5;color:var(--text)}
.service-card.active p{color:#fbe3d8}
.service-icon{width:54px;height:54px}

/* projects */
.projects-copy{left:110px;top:2290px;width:440px}
.projects-copy p{margin-top:24px}
.projects-photo{left:580px;top:2255px;width:490px;height:445px;border-radius:22px;background:linear-gradient(150deg,#f1ce7e 0%,#c9a67b 40%,#6f7f96 100%)}

/* clients */
.clients-bg{left:0;top:2740px;width:1200px;height:330px;background:linear-gradient(180deg,#fff 0%,#eef1f4 55%,#d9dee4 100%)}
.clients-title{left:0;top:2810px;width:1200px;text-align:center}
.client-row{left:110px;top:2900px;display:flex;gap:20px}
.client-box{width:230px;height:90px;background:var(--white);border:1px solid var(--line);border-radius:6px;display:flex;flex-direction:column;align-items:center;justify-content:center;gap:8px;font-size:15px;color:var(--ink);box-shadow:0 4px 10px rgba(0,0,0,.06)}

/* newsletter */
.newsletter{left:110px;top:3070px;width:980px;height:220px;background:var(--white);border-radius:6px;box-shadow:0 6px 20px rgba(0,0,0,.08);z-index:2}
.newsletter h2{position:absolute;left:0;top:86px;font-size:33px;font-weight:700;line-height:1.2;text-transform:uppercase}
.newsletter p{position:absolute;left:420px;top:50px;width:540px;font-size:14px;line-height:1.5;color:var(--text)}
.nl-form{position:absolute;left:420px;top:126px;display:flex;gap:16px}
.nl-input{width:300px;height:40px;border:1px solid var(--line);border-radius:4px;font-size:12px;color:#999;padding:12px 16px}
.nl-submit{height:40px;background:var(--orange-deep);color:var(--white);font-size:13px;padding:12px 24px;border-radius:4px}

/* footer */
.site-footer{left:0;top:3280px;width:1200px;height:296px;background:var(--footer);color:var(--white);text-align:center}
.footer-brand{position:absolute;left:0;top:46px;width:1200px;display:flex;justify-content:center;align-items:center;gap:14px}
.footer-brand .brand-name{color:var(--white);font-size:30px}
.footer-brand .brand-dot{background:var(--white)}
.footer-nav{position:absolute;left:0;top:200px;width:1200px;display:flex;justify-content:center;gap:52px;font-size:16px}
.copyright{position:absolute;left:0;top:252px;width:1200px;font-size:14px}
</style>
</head>
<body>

<header class="site-header abs">
  <div class="brand abs"><span class="brand-dot"></span><span class="brand-name">Kovadrel<br>Limited</span></div>
  <div class="phone-pill abs">
    <svg width="14" height="14" viewBox="0 0 24 24" fill="#fff"><path d="M6.6 10.8a15 15 0 0 0 6.6 6.6l2.2-2.2c.3-.3.7-.4 1-.2 1.1.4 2.3.6 3.6.6.6 0 1 .4 1 1V20c0 .6-.4 1-1 1A17 17 0 0 1 3 4c0-.6.4-1 1-1h3.5c.6 0 1 .4 1 1 0 1.3.2 2.5.6 3.6.1.3 0 .7-.2 1z"/></svg>
    +254 700 000 123
  </div>
  <nav class="main-nav abs"><a>Home</a><a>About Us</a><a>Services</a><a>What We Do</a><a>Contact Us</a></nav>
</header>

<section class="hero abs"></section>
<div class="hero-media abs" role="img" aria-label="Engineers in hard hats and safety glasses shown in a tiled collage"></div>
<div class="hero-copy abs">
  <h1>Welcome to<br>Kovadrel<br>Limited</h1>
  <p>Lorem Ipsum is simply dummy text of the printing and typesetting industry. Lorem Ipsum</p>
  <span class="btn light">Get Started Now</span>
</div>

<div class="peach-circle abs" style="left:40px;top:1240px;width:120px;height:120px"></div>
<div class="about-photo abs" role="img" aria-label="Two workers in blue overalls and hard hats at an industrial plant"></div>
<section class="about-copy abs">
  <h2 class="section-title">ABOUT US</h2>
  <p class="body-text">Kovadrel undertakes Design, Supply, Installation and Commissioning of LPG and Petroleum systems including LPG Reticulated Systems (piped gas). We also do LPG tank revalidation and recertification.</p>
  <p class="body-text">Our clients include Oil companies (both multinationals and local), government agencies, manufacturing companies, agricultural institutions, and the building services industry.</p>
  <span class="btn" style="margin-top:26px">Read More</span>
</section>

<section class="services-band abs"></section>
<div class="services-intro abs">
  <h2 class="section-title">WHAT WE DO</h2>
  <p class="body-text">Lorem Ipsum is simply dummy text of the printing and typesetting industry. Lorem Ipsum has been the industry's standard dummy text ever since the 1500s, when an unknown</p>
  <span class="btn light">View More</span>
</div>

<div class="service-card active abs" style="left:510px;top:1480px">
  <svg class="service-icon" viewBox="0 0 54 54" fill="none" stroke="#fff" stroke-width="2.5"><circle cx="27" cy="27" r="9"/><path d="M27 6v8M27 40v8M6 27h8M40 27h8M12 12l6 6M36 36l6 6M42 12l-6 6M18 36l-6 6"/></svg>
  <h3>Engineering &amp; Procurement</h3>
  <p>Lorem Ipsum is simply dummy text of the printing and typesetting industry. Lorem Ipsum has been</p>
</div>
<div class="service-card abs" style="left:818px;top:1480px">
  <svg class="service-icon" viewBox="0 0 54 54" fill="none" stroke="#333" stroke-width="2.5"><path d="M6 46h42M10 46V30h8v16M23 46V22h8v24M36 46V12h8v34"/><path d="M8 24l14-10 10 6 14-12"/></svg>
  <h3>Construction &amp; Automation</h3>
  <p>Lorem Ipsum is simply dummy text of the printing and typesetting industry. Lorem Ipsum has been</p>
</div>
<div class="service-card abs" style="left:495px;top:1775px">
  <svg class="service-icon" viewBox="0 0 54 54" fill="none" stroke="#333" stroke-width="2.5"><rect x="12" y="8" width="30" height="40" rx="3"/><path d="M21 6h12v6H21zM18 22l3 3 5-5M30 23h8M18 34l3 3 5-5M30 35h8"/></svg>
  <h3>Non-Destructive Testing</h3>
  <p>Lorem Ipsum is simply dummy text of the printing and typesetting industry. Lorem Ipsum has been</p>
</div>
<div class="service-card abs" style="left:803px;top:1775px">
  <svg class="service-icon" viewBox="0 0 54 54" fill="none" stroke="#333" stroke-width="2.5"><circle cx="27" cy="16" r="7"/><path d="M8 34c6 0 10 6 19 6s13-6 19-6M8 42c6 0 10 6 19 6s13-6 19-6"/></svg>
  <h3>Training</h3>
  <p>Lorem Ipsum is simply dummy text of the printing and typesetting industry. Lorem Ipsum has been</p>
</div>

<section class="projects-copy abs">
  <h2 class="section-title">OUR PROJECTS</h2>
  <p class="body-text">Kovadrel undertakes Design, Supply, Installation and Commissioning of LPG and Petroleum systems including LPG Reticulated Systems (piped gas). We also do LPG tank revalidation and recertification.</p>
  <p class="body-text">Our clients include Oil companies (both multinationals and local), government agencies, manufacturing companies, agricultural institutions, and the building services industry.</p>
  <span class="btn" style="margin-top:30px">View More</span>
</section>
<div class="projects-photo abs" role="img" aria-label="Engineers in hard hats and safety vests reviewing plans at a table"></div>
<div class="peach-circle abs" style="left:1060px;top:2630px;width:140px;height:140px;border-radius:70px 0 0 70px"></div>

<div class="clients-bg abs" role="img" aria-label="Faded view of an industrial refinery skyline"></div>
<h2 class="section-title clients-title abs">OUR CLIENTS</h2>
<div class="client-row abs">
  <div class="client-box"><svg width="30" height="24" viewBox="0 0 30 24" fill="none" stroke="#444" stroke-width="2"><path d="M2 22h26M6 22V10h18v12M10 10V4h10v6"/></svg>LPG/ Petroleum Companies</div>
  <div class="client-box"><svg width="30" height="24" viewBox="0 0 30 24" fill="none" stroke="#444" stroke-width="2"><path d="M3 22V6h24v16M2 22h26M15 9v8M11 13h8"/></svg>Hospitals</div>
  <div class="client-box"><svg width="30" height="24" viewBox="0 0 30 24" fill="none" stroke="#444" stroke-width="2"><path d="M2 22h26M4 22V8l6 4V8l6 4V8l6 4v10"/></svg>LPG Reticulation/ Piped Gas</div>
  <div class="client-box"><svg width="30" height="24" viewBox="0 0 30 24" fill="none" stroke="#444" stroke-width="2"><path d="M2 22h26M5 22V4h20v18M9 8h4M17 8h4M9 13h4M17 13h4"/></svg>Industries / Hotels</div>
</div>

<section class="newsletter abs">
  <h2 style="left:30px">Subscribe to<br>our newsletter</h2>
  <p>Lorem Ipsum is simply dummy text of the printing and typesetting industry. Lorem Ipsum has been the industry's standard</p>
  <div class="nl-form"><div class="nl-input">Your Email Address</div><div class="nl-submit">Subscribe</div></div>
</section>

<footer class="site-footer abs">
  <div class="footer-brand"><span class="brand-dot"></span><span class="brand-name">Kovadrel Limited</span></div>
  <nav class="footer-nav"><span>Home</span><span>About Us</span><span>Services</span><span>What We Do</span><span>Contact Us</span></nav>
  <p class="copyright">Copyright © 2023 Kovadrel Limited | All rights reserved.</p>
</footer>

</body>
</html>
```